Veltrano.co - Polar Expeditions Specialists

We need a modern, visually striking business card for Veltrano.co, a company specialized in selling expedition cruises to the most remote regions on Earth, with a focus on the Arctic and Antarctica. The design should instantly communicate that the cardholder is an expert in polar travel. Use clean, premium aesthetics with cool tones like icy blue and white, possibly incorporating polar imagery (ice, glaciers, penguins, etc.)

Attached the logo

Contact Information for Business Card

Feels high-end and trustworthy.. Visually memorable — encourages people to keep it

Colors
0054AA
0677BA
7BADD7
CADEEF
E8F1F8

Requirements
Must have
• ice, glaciers, penguins, montains
Nice to have
• modern, transparente,

```html
<!DOCTYPE html>
<html lang="en">
<head>
<meta charset="utf-8">
<title>Veltrano.co – Business Card</title>
<link href="https://fonts.googleapis.com/css2?family=Poppins:wght@400;500;700&display=swap" rel="stylesheet">
<style>
  :root {
    --stage: #e9eef4;
    --brand-blue: #3474b4;
    --brand-blue-light: #6f9fce;
    --brand-blue-deep: #2f6aa8;
    --card-white: #ffffff;
    --line-blue: #7ba5d1;
  }
  * { box-sizing: border-box; margin: 0; padding: 0; }
  html, body { width: 1200px; height: 1200px; overflow: hidden; }
  body {
    background: var(--stage);
    font-family: "Poppins", sans-serif;
    position: relative;
  }
  .card {
    position: absolute;
    top: 303px;
    height: 594px;
    overflow: hidden;
    text-align: center;
  }
  .card-front {
    left: 200px;
    width: 369px;
    background: linear-gradient(180deg, var(--brand-blue) 0%, var(--brand-blue) 45%, var(--brand-blue-light) 100%);
    color: var(--card-white);
  }
  .card-back {
    left: 599px;
    width: 364px;
    background: var(--card-white);
    color: var(--brand-blue);
  }
  .front-decoration {
    position: absolute;
    left: 0; right: 0; bottom: 0;
    height: 280px;
    background: radial-gradient(ellipse at 30% 70%, rgba(47,106,168,0.55) 0%, rgba(47,106,168,0) 60%),
                radial-gradient(ellipse at 85% 85%, rgba(47,106,168,0.5) 0%, rgba(47,106,168,0) 55%);
  }
  .brand-dot {
    position: absolute;
    left: 50%;
    width: 72px; height: 72px;
    margin-left: -36px;
    border-radius: 50%;
  }
  .card-front .brand-dot { top: 110px; background: var(--card-white); }
  .card-back .brand-dot { top: 64px; background: var(--brand-blue); }
  .brand-name {
    position: absolute;
    left: 0; right: 0;
    font-weight: 700;
    line-height: 1;
    letter-spacing: -0.5px;
  }
  .card-front .brand-name { top: 218px; font-size: 56px; }
  .card-back .brand-name { top: 166px; font-size: 50px; }
  .tagline {
    position: absolute;
    left: 0; right: 0;
    font-weight: 500;
    line-height: 1;
  }
  .card-front .tagline { top: 279px; font-size: 16.5px; }
  .card-back .tagline { top: 222px; font-size: 15px; }
  .holder-name {
    position: absolute; left: 0; right: 0; top: 334px;
    font-size: 27px; font-weight: 700; line-height: 1;
  }
  .holder-role {
    position: absolute; left: 0; right: 0; top: 363px;
    font-size: 16px; font-weight: 400; line-height: 1; letter-spacing: 0.3px;
  }
  .contact-icons {
    position: absolute; left: 0; right: 0; top: 395px;
    display: flex; justify-content: center; align-items: center; gap: 4px;
  }
  .contact-icons .rule { width: 46px; height: 1px; background: var(--line-blue); margin: 0 6px; }
  .icon-box {
    width: 25px; height: 25px; border-radius: 3px;
    background: var(--brand-blue);
    display: flex; align-items: center; justify-content: center;
  }
  .contact-lines {
    position: absolute; left: 0; right: 0; top: 427px;
    font-size: 17.5px; line-height: 21px;
  }
  .divider {
    position: absolute; left: 88px; width: 189px; top: 507px;
    height: 1px; background: var(--line-blue);
  }
  .address {
    position: absolute; left: 0; right: 0; top: 519px;
    font-size: 17.5px; line-height: 21px;
  }
</style>
</head>
<body>
  <section class="card card-front">
    <div class="front-decoration" role="img" aria-label="Faint silhouettes of penguins in darker blue"></div>
    <div class="brand-dot"></div>
    <h1 class="brand-name">Veltrano.co</h1>
    <p class="tagline">Polar Expeditions Specialists</p>
  </section>

  <section class="card card-back">
    <div class="brand-dot"></div>
    <h2 class="brand-name">Veltrano.co</h2>
    <p class="tagline">Polar Expeditions Specialists</p>

    <p class="holder-name">Marcus Hale</p>
    <p class="holder-role">MANAGING DIRECTOR</p>

    <div class="contact-icons">
      <span class="rule"></span>
      <span class="icon-box">
        <svg width="15" height="15" viewBox="0 0 24 24"><path fill="#fff" d="M6.6 10.8a15.1 15.1 0 0 0 6.6 6.6l2.2-2.2a1 1 0 0 1 1-.25 11.4 11.4 0 0 0 3.6.57 1 1 0 0 1 1 1V20a1 1 0 0 1-1 1A17 17 0 0 1 3 4a1 1 0 0 1 1-1h3.5a1 1 0 0 1 1 1c0 1.25.2 2.45.57 3.6a1 1 0 0 1-.25 1z"/></svg>
      </span>
      <span class="icon-box">
        <svg width="16" height="12" viewBox="0 0 16 12"><rect x="0.75" y="0.75" width="14.5" height="10.5" fill="none" stroke="#fff" stroke-width="1.2"/><path d="M1 1l7 6 7-6M1 11l5-4.5M15 11l-5-4.5" fill="none" stroke="#fff" stroke-width="1.1"/></svg>
      </span>
      <span class="icon-box">
        <svg width="15" height="15" viewBox="0 0 16 16"><circle cx="8" cy="8" r="6.8" fill="none" stroke="#fff" stroke-width="1.3"/><ellipse cx="8" cy="8" rx="3" ry="6.8" fill="none" stroke="#fff" stroke-width="1"/><path d="M1.2 8h13.6" stroke="#fff" stroke-width="1"/></svg>
      </span>
      <span class="rule"></span>
    </div>

    <div class="contact-lines">
      <p>055-210 384 617</p>
      <p>hello@mailnorth.com</p>
      <p>www.veltranotrips.com</p>
    </div>

    <div class="divider"></div>

    <div class="address">
      <p>18, Harbour Lane, Suite 4</p>
      <p>90317, Norland</p>
    </div>
  </section>
</body>
</html>
```